Navoro & Omvar Automotive Repair Shop. Need a new website design.

We specialize in Navoro & Omvar auto repair, but also work on other Asian import vehicles. We have been in business for 7 years and pride ourselves on high quality auto repair that is fixed right the first time. Would like the automotive repair website to incorporate the colors black, red and white if possible and have our logo and some Navoro and Omvar vehicles included in the website.

Target Market(s)

Navoro & Omvar vehicle owners

Industry/Entity Type

Automotive Repair

Coding

Coded - Design and coding required

Number of Pages Required

5+ page

Colors
EB3D1F
EC4F4E
F09395
F8D3D4
FCEDEE

Requirements
Must have
• Home, Services, Contact Us, Schedule appointment, and a gallery tab that I can add shop pictures to when completed.
Nice to have
• Would like to see example pictures of job next to each service listed.
Should not have
• Service not related to auto repair. Ex. auto detailing, towing, car wash

```html
<!DOCTYPE html>
<html lang="en">
<head>
<meta charset="utf-8">
<title>Halden Automotive – Navoro &amp; Omvar Repair</title>
<link rel="stylesheet" href="https://fonts.googleapis.com/css2?family=Michroma&family=Poppins:wght@400;500;600&display=swap">
<style>
:root{
  --red:#EB3D1F;
  --red-soft:#EC4F4E;
  --pink-mid:#F09395;
  --pink-light:#F8D3D4;
  --pink-bg:#FCEDEE;
  --black:#111111;
  --footer:#2a2a2a;
  --white:#ffffff;
  --text:#333333;
  --muted:#666666;
}
*{margin:0;padding:0;box-sizing:border-box}
html,body{width:1200px;height:4961px;overflow:hidden}
body{position:relative;background:var(--white);font-family:"Poppins",sans-serif;color:var(--text)}
.abs{position:absolute}
.display{font-family:"Michroma",sans-serif;font-weight:400}
.btn{position:absolute;background:var(--red);color:var(--white);font-size:12px;font-weight:500;display:flex;align-items:center;justify-content:center;box-shadow:4px 4px 0 var(--pink-light)}
.photo{position:absolute}

/* header */
.topbar{left:540px;top:0;width:660px;height:40px;background:var(--red);clip-path:polygon(3% 0,100% 0,100% 100%,0 100%);color:var(--white);font-size:10px}
.topbar .hours{position:absolute;left:72px;top:12px}
.topbar .follow{position:absolute;left:335px;top:12px}
.topbar .social{position:absolute;top:13px;width:12px;height:12px;border-radius:50%;background:var(--white)}
.brand{left:122px;top:30px;display:flex;align-items:center;gap:8px;font-weight:600;font-size:22px;color:var(--black)}
.brand .mark{width:22px;height:22px;border-radius:50%;background:var(--red)}
.contact-item{top:58px;font-size:10px;line-height:16px;display:flex;gap:10px}
.contact-item b{font-weight:600;color:var(--black)}
.nav{left:333px;top:117px;width:867px;height:39px;background:var(--black);clip-path:polygon(3% 0,100% 0,100% 100%,0 100%);color:var(--white);font-size:10px}
.nav ul{list-style:none;display:flex;gap:28px;position:absolute;left:50px;top:12px}

/* hero */
.hero{left:0;top:160px;width:1200px;height:535px;background:linear-gradient(100deg,#1d1f22 0%,#3a3c3f 45%,#b4621a 70%,#3b3329 100%)}
.hero h1{position:absolute;left:125px;top:162px;color:var(--white);font-size:42px;line-height:56px}
.hero p{position:absolute;left:125px;top:285px;width:360px;color:var(--white);font-size:12px;line-height:18px}

/* about */
.about-photo{left:189px;top:814px;width:416px;height:361px;background:linear-gradient(135deg,#6f6a5e,#3c3a35 55%,#a9773e)}
.dots{left:155px;top:900px;width:30px;height:180px;background-image:radial-gradient(var(--red) 1.6px,transparent 2px);background-size:10px 10px}
.about h2{position:absolute;left:672px;top:790px;font-size:38px;line-height:50px;color:var(--black)}
.about p{position:absolute;left:672px;width:400px;font-size:11px;line-height:17px;color:var(--text)}

/* elevate */
.band-pink{left:0;width:1200px;background:var(--pink-bg)}
.section-title{left:0;width:1200px;text-align:center;color:var(--black);font-size:38px;line-height:50px}
.carousel-dot{top:2158px;width:12px;height:12px;border-radius:50%;background:var(--red)}

/* services */
.services-title{left:125px;top:2360px;font-size:38px;line-height:50px;color:var(--black)}
.divider{left:547px;top:2384px;width:1px;height:56px;background:#999}
.services-intro{left:722px;top:2382px;width:350px;font-size:11px;line-height:17px}
.svc-card{position:absolute;top:2689px;width:230px;height:178px;background:var(--white);padding:22px 18px;box-shadow:0 8px 22px rgba(0,0,0,.08)}
.svc-card h3{font-size:15px;font-weight:500;color:var(--black);margin-bottom:10px}
.svc-card p{font-size:10px;line-height:15px;color:var(--muted)}
.svc-card a{display:block;margin-top:10px;font-size:9px;color:var(--red);text-decoration:none}

/* gallery */
.gallery-intro{left:340px;top:3170px;width:520px;text-align:center;font-size:11px;line-height:17px}

/* partners */
.partner{top:3985px;height:70px;border-radius:8px;background:#e9e9e9}
.partner-dot{top:4016px;width:10px;height:10px;border-radius:50%;background:var(--red)}

/* contact */
.footer{left:0;top:4445px;width:1200px;height:516px;background:var(--footer)}
.contact-box{left:125px;top:4175px;width:950px;height:362px;background:var(--red)}
.contact-box h2{position:absolute;left:80px;top:62px;color:var(--white);font-size:42px;line-height:46px}
.contact-box .line{position:absolute;left:80px;color:var(--white);font-size:12px;display:flex;align-items:center;gap:10px}
.field{position:absolute;left:464px;width:404px;background:var(--white);font-size:11px;color:#777;padding:11px 14px}
.send{position:absolute;top:4422px;width:50px;height:38px;background:var(--red)}

/* footer */
.f-head{font-family:"Michroma",sans-serif;font-weight:400;color:var(--white);font-size:20px}
.f-links{left:172px;top:4662px;list-style:none;color:var(--white);font-size:11px;line-height:39.5px}
.f-brand{left:520px;top:4612px;width:166px;display:flex;align-items:center;justify-content:center;gap:8px;color:var(--white);font-weight:600;font-size:22px}
.f-brand .mark{width:22px;height:22px;border-radius:50%;background:var(--red)}
.f-social{top:4738px;width:26px;height:26px;border-radius:50%;border:1.5px solid var(--white)}
.f-copy{left:300px;top:4826px;width:606px;text-align:center;color:var(--white);font-size:11px}
.f-legal{left:300px;top:4860px;width:606px;text-align:center;color:var(--white);font-size:11px;font-weight:600}
.f-contact{left:880px;width:250px;color:var(--white);font-size:10px;line-height:16px;display:flex;gap:22px;align-items:flex-start}
</style>
</head>
<body>

<!-- header -->
<div class="abs topbar">
  <span class="hours">Work Open Mon - Sat 8:00 - 17:00</span>
  <span class="follow">Follow Us On :</span>
  <span class="social" style="left:420px"></span>
  <span class="social" style="left:446px"></span>
  <span class="social" style="left:472px"></span>
  <span class="social" style="left:498px"></span>
</div>
<div class="abs brand"><span class="mark"></span>HALDEN</div>
<div class="abs contact-item" style="left:383px">
  <svg width="16" height="16" viewBox="0 0 24 24" fill="none" stroke="#EB3D1F" stroke-width="2"><path d="M5 3h4l2 5-3 2a11 11 0 0 0 6 6l2-3 5 2v4a2 2 0 0 1-2 2A17 17 0 0 1 3 5a2 2 0 0 1 2-2z"/></svg>
  <div><b>Call Us</b><br>123-456-789</div>
</div>
<div class="abs contact-item" style="left:578px">
  <svg width="16" height="16" viewBox="0 0 24 24" fill="none" stroke="#EB3D1F" stroke-width="2"><rect x="3" y="5" width="18" height="14"/><path d="M3 6l9 7 9-7"/></svg>
  <div><b>Send Via Mail</b><br>Loremipsum@haldenautomotive.com</div>
</div>
<div class="btn" style="left:930px;top:61px;width:145px;height:36px;box-shadow:none">Contact Us</div>
<nav class="abs nav">
  <ul><li>Home</li><li>Services</li><li>Gallery</li><li>Contact Us</li><li>Schedule appointment</li></ul>
  <svg class="abs" style="left:785px;top:12px" width="14" height="14" viewBox="0 0 24 24" fill="none" stroke="#fff" stroke-width="2"><circle cx="10" cy="10" r="7"/><path d="M15 15l6 6"/></svg>
  <svg class="abs" style="left:822px;top:12px" width="14" height="14" viewBox="0 0 24 24" fill="none" stroke="#fff" stroke-width="2"><path d="M2 3h4l3 12h11l2-8H7"/><circle cx="10" cy="20" r="1.5"/><circle cx="18" cy="20" r="1.5"/></svg>
</nav>

<!-- hero -->
<section class="abs hero" role="img" aria-label="Orange sports coupe parked in front of a modern building at dusk">
  <h1 class="display">We Fix, You Drive<br>with Confidence.</h1>
  <p>Lorem Ipsum is simply dummy text of the printing and typesetting industry.</p>
  <div class="btn" style="left:125px;top:360px;width:205px;height:30px">Schedule Appointment</div>
</section>

<!-- about -->
<section class="about">
  <div class="abs dots"></div>
  <div class="photo about-photo" role="img" aria-label="Car engine and transmission on a workshop lift"></div>
  <h2 class="display">About Halden<br>Automotive</h2>
  <p style="top:898px">Led by an NCT master certified technician with 20 years experience working for Navoro &amp; Omvar dealerships, our auto shop is sure go to facility for everything from factory auto maintenance, including oil changes, fluid services and tune ups, to complex engine repairs, hybrid diagnostics &amp; repair, brake jobs, etc.</p>
  <p style="top:1030px">We have state of the art equipment and tools to ensure that we can properly diagnose and repair your vehicles get you back on the road quickly. Our work comes with a warranty and we offer towing if needed. We also offer discounts for Kestrip &amp; Farlowe rides.</p>
  <div class="btn" style="left:672px;top:1161px;width:153px;height:29px">Learn More</div>
</section>

<!-- elevate -->
<div class="abs band-pink" style="top:1292px;height:980px"></div>
<h2 class="abs section-title display" style="top:1385px">Elevate Your Drive with<br>Specialized Repairs.</h2>
<div class="photo" style="left:0;top:1556px;width:375px;height:514px;background:linear-gradient(120deg,#6c5a3d,#2a2a2c 50%,#8a7355)" role="img" aria-label="Dark sedan driving along a road"></div>
<div class="photo" style="left:825px;top:1556px;width:375px;height:514px;background:linear-gradient(160deg,#8d949a,#3b4552 55%,#2b3340)" role="img" aria-label="Blue wagon parked beside a glass building"></div>
<div class="photo" style="left:375px;top:1522px;width:450px;height:512px;background:linear-gradient(180deg,#2d2e31,#141518 60%,#232426);box-shadow:0 10px 30px rgba(0,0,0,.3)" role="img" aria-label="Front view of a dark Omvar SUV"></div>
<span class="abs carousel-dot" style="left:508px"></span>
<span class="abs carousel-dot" style="left:538px"></span>
<span class="abs carousel-dot" style="left:568px"></span>
<span class="abs carousel-dot" style="left:598px"></span>
<span class="abs carousel-dot" style="left:628px"></span>
<span class="abs carousel-dot" style="left:658px"></span>

<!-- services -->
<h2 class="abs services-title display">OUR<br>SERVICES</h2>
<div class="abs divider"></div>
<p class="abs services-intro">Lorem Ipsum is simply dummy text of the printing and typesetting industry. Lorem Ipsum is simply dummy text of the printing and typesetting industry.</p>
<div class="photo" style="left:122px;top:2500px;width:306px;height:278px;background:linear-gradient(140deg,#8b8f93,#3d4145 60%,#c9ccd0)" role="img" aria-label="Mechanic changing oil under a raised car"></div>
<div class="photo" style="left:444px;top:2500px;width:306px;height:278px;background:linear-gradient(140deg,#5a5c5f,#2c2d2f 55%,#7d6a55)" role="img" aria-label="Open engine bay during repair"></div>
<div class="photo" style="left:770px;top:2500px;width:305px;height:278px;background:linear-gradient(140deg,#6b7681,#34393f 55%,#a9b0b8)" role="img" aria-label="Car on a lift in the service bay"></div>
<div class="svc-card" style="left:167px"><h3>Oil Changes</h3><p>Lorem Ipsum is simply dummy text of the printing and typesetting industry. Lorem Ipsum is simpl</p><a>READ MORE ↗</a></div>
<div class="svc-card" style="left:490px"><h3>Engine Repair</h3><p>Lorem Ipsum is simply dummy text of the printing and typesetting industry. Lorem Ipsum is simpl</p><a>READ MORE ↗</a></div>
<div class="svc-card" style="left:815px"><h3>Brake Service</h3><p>Lorem Ipsum is simply dummy text of the printing and typesetting industry. Lorem Ipsum is simpl</p><a>READ MORE ↗</a></div>

<!-- gallery -->
<div class="abs band-pink" style="top:2967px;height:894px"></div>
<h2 class="abs section-title display" style="top:3058px">OUR<br>GALLERY</h2>
<p class="abs gallery-intro">Lorem Ipsum is simply dummy text of the printing and typesetting industry. Lorem Ipsum is simply dummy text of the printing and typesetting industry.</p>
<div class="photo" style="left:0;top:3347px;width:230px;height:236px;background:linear-gradient(135deg,#7a7f84,#3a3d40)" role="img" aria-label="Technician working in an engine bay"></div>
<div class="photo" style="left:250px;top:3300px;width:197px;height:206px;background:linear-gradient(135deg,#5f5550,#2d2a28)" role="img" aria-label="Engine parts on a workbench"></div>
<div class="photo" style="left:250px;top:3517px;width:197px;height:114px;background:linear-gradient(135deg,#8e949a,#3c4a5a)" role="img" aria-label="Cars in the workshop bays"></div>
<div class="photo" style="left:464px;top:3256px;width:275px;height:419px;background:linear-gradient(180deg,#9fb6cc 0%,#c5d2dd 35%,#4a4a4c 55%,#5e5f61 100%)" role="img" aria-label="Shop building exterior with cars parked outside"></div>
<div class="photo" style="left:753px;top:3300px;width:197px;height:120px;background:linear-gradient(135deg,#96a0a9,#3d5068)" role="img" aria-label="Vehicle raised on a blue lift"></div>
<div class="photo" style="left:753px;top:3434px;width:197px;height:197px;background:linear-gradient(135deg,#6e7277,#2c2f33)" role="img" aria-label="Underside of a car during service"></div>
<div class="photo" style="left:967px;top:3347px;width:233px;height:236px;background:linear-gradient(135deg,#5a6470,#262a2f)" role="img" aria-label="Engine bay under repair with hood open"></div>
<div class="btn" style="left:525px;top:3731px;width:150px;height:30px">See More</div>

<!-- partners -->
<div class="abs partner" style="left:-20px;width:125px"></div>
<span class="abs partner-dot" style="left:175px"></span>
<div class="abs partner" style="left:250px;width:205px;height:50px;top:3995px"></div>
<span class="abs partner-dot" style="left:510px"></span>
<div class="abs partner" style="left:590px;width:110px;height:110px;top:3965px;border-radius:50%"></div>
<span class="abs partner-dot" style="left:770px"></span>
<div class="abs partner" style="left:845px;width:185px;height:46px;top:3997px"></div>
<span class="abs partner-dot" style="left:1093px"></span>
<div class="abs partner" style="left:1165px;width:80px;height:80px;top:3980px;border-radius:50%"></div>

<!-- footer + contact -->
<footer class="abs footer"></footer>
<section class="abs contact-box">
  <h2 class="display">Contact Us<br>For More<br>Updates</h2>
  <div class="line" style="top:239px">
    <svg width="16" height="16" viewBox="0 0 24 24" fill="none" stroke="#fff" stroke-width="2"><rect x="3" y="5" width="18" height="14"/><path d="M3 6l9 7 9-7"/></svg>Loremipsum@haldenautomotive.com</div>
  <div class="line" style="top:275px">
    <svg width="16" height="16" viewBox="0 0 24 24" fill="none" stroke="#fff" stroke-width="2"><path d="M5 3h4l2 5-3 2a11 11 0 0 0 6 6l2-3 5 2v4a2 2 0 0 1-2 2A17 17 0 0 1 3 5a2 2 0 0 1 2-2z"/></svg>123-456-789</div>
  <div class="field" style="top:67px;height:42px">Name</div>
  <div class="field" style="top:125px;height:42px">Email</div>
  <div class="field" style="top:186px;height:112px">Message</div>
</section>
<div class="abs send" style="left:940px">
  <svg style="margin:11px 0 0 17px" width="16" height="16" viewBox="0 0 24 24" fill="none" stroke="#fff" stroke-width="2.4"><path d="M3 12l18-9-7 18-3-7z"/></svg>
</div>

<h4 class="abs f-head" style="left:172px;top:4608px">Quick Links</h4>
<ul class="abs f-links"><li>Home</li><li>Services</li><li>Gallery</li><li>Schedule an Appointment</li><li>Contact Us</li></ul>
<div class="abs f-brand"><span class="mark"></span>HALDEN</div>
<span class="abs f-social" style="left:508px"></span>
<span class="abs f-social" style="left:563px"></span>
<span class="abs f-social" style="left:618px"></span>
<span class="abs f-social" style="left:673px"></span>
<p class="abs f-copy">© Copyright 2023 <b>LOREM IPSUM.</b> All rights reserved</p>
<p class="abs f-legal">Privacy Policy &nbsp;|&nbsp; Sitemap</p>
<h4 class="abs f-head" style="left:880px;top:4608px">Contact Us</h4>
<div class="abs f-contact" style="top:4668px">
  <svg width="14" height="14" viewBox="0 0 24 24" fill="#fff"><path d="M12 2a7 7 0 0 0-7 7c0 5 7 13 7 13s7-8 7-13a7 7 0 0 0-7-7zm0 9.5A2.5 2.5 0 1 1 12 6.5a2.5 2.5 0 0 1 0 5z"/></svg>
  <span>Lorem Ipsum is simply dummy text of the prpri</span></div>
<div class="abs f-contact" style="top:4744px">
  <svg width="14" height="14" viewBox="0 0 24 24" fill="#fff"><path d="M3 12l18-9-7 18-3-7z"/></svg>
  <span>hello@loremipsum.com</span></div>
<div class="abs f-contact" style="top:4812px">
  <svg width="14" height="14" viewBox="0 0 24 24" fill="#fff"><path d="M5 3h4l2 5-3 2a11 11 0 0 0 6 6l2-3 5 2v4a2 2 0 0 1-2 2A17 17 0 0 1 3 5a2 2 0 0 1 2-2z"/></svg>
  <span>123-456-789</span></div>

</body>
</html>
```